Develop website for Cloud Security Startup

Looking for a logo that conveys the outsourced security and management of clients data, systems and development in Tellix, Bri and Pindle with an emphasis on security and compliance

Target Market(s)

Companies looking for professional services IT firm

Coding

Coded - Design and coding required

Number of Pages Required

5+ page

Font styles to use
Sans Serif

Colors
0455a3
33a6d7

Requirements
Must have
• Landing Page
- Help me get started

Move to the cloud safely
- Benefits of Cloud

What we do
- Cloud Adoption
- Managed Services
- Optimise

Resources
- News
- Resources
- Events
- Webinars
- Not for profit
- Case Studies
- Support Button
- Incident Button

Company
- About Us
- Why Vorplexa?
- Acreditations
- Quorvane Tellix Partner
- Net Promoter Score
- Careers
- Contact Us

Contact Us

```html
<!DOCTYPE html>
<html lang="en">
<head>
<meta charset="utf-8">
<title>Vorplexa Effective Technology Management</title>
<link href="https://fonts.googleapis.com/css2?family=Baloo+2:wght@600;700;800&family=Arimo:wght@400;700&display=swap" rel="stylesheet">
<style>
:root{
  --navy:#06127a;
  --deep:#0455a3;
  --sky:#33a6d7;
  --bright:#1fa3e3;
  --ink:#111;
  --pale:#b9e7f6;
  --night:#06142a;
  --white:#fff;
}
*{margin:0;padding:0;box-sizing:border-box}
html,body{width:1200px;height:3249px;overflow:hidden}
body{position:relative;font-family:"Arimo",Arial,sans-serif;color:var(--ink);background:var(--white)}
.head{font-family:"Baloo 2","Arial Black",sans-serif;font-weight:800;letter-spacing:.3px}
a{color:inherit;text-decoration:none}

/* header */
.site-header{position:absolute;left:0;top:0;width:1200px;height:82px;background:var(--white)}
.brand{position:absolute;left:138px;top:26px;display:flex;align-items:center;gap:8px;font-family:"Baloo 2",sans-serif;font-weight:700;font-size:22px;color:var(--deep)}
.brand-dot{width:16px;height:16px;border-radius:50%;background:var(--deep)}
.main-nav{position:absolute;top:32px;left:316px;display:flex;gap:36px;font-family:"Baloo 2",sans-serif;font-weight:600;font-size:16px;color:#111}
.main-nav .caret::after{content:"";display:inline-block;margin-left:5px;border:4.5px solid transparent;border-top:5px solid #111;vertical-align:1px}
.nav-active{position:absolute;left:314px;top:78px;width:47px;height:4px;background:var(--navy)}
.social{position:absolute;display:flex;gap:14px}
.social span{width:12px;height:12px;border-radius:50%;background:#111}
.header-social{left:964px;top:35px}

/* hero */
.hero{position:absolute;left:0;top:82px;width:1200px;height:602px;overflow:hidden}
.hero-photo{position:absolute;inset:0;background:linear-gradient(110deg,#0a0f18 0%,#1d2a38 40%,#2d4a5a 60%,#121c26 100%)}
.hero-title{position:absolute;left:110px;top:170px;color:var(--white);font-size:47px;line-height:56px}
.hero-text{position:absolute;left:112px;top:296px;width:490px;color:var(--white);font-size:14px;line-height:30px}
.btn{position:absolute;display:flex;align-items:center;gap:6px;border-radius:22px;color:var(--white);font-family:"Baloo 2",sans-serif;font-weight:700;font-size:16px;padding:0 16px;height:42px;background:linear-gradient(90deg,var(--bright),var(--deep))}
.btn svg{width:14px;height:14px}
.hero .btn{left:111px;top:374px}
.hero-wave{position:absolute;left:0;bottom:0;width:1200px;height:90px}

/* what we do */
.section-title{position:absolute;left:0;width:1200px;text-align:center;font-size:36px;color:#111}
.services{position:absolute;left:0;top:684px;width:1200px;height:792px}
.services .section-title{top:70px}
.service-card{position:absolute;top:169px;width:293px;height:537px;border-radius:147px;background:linear-gradient(180deg,var(--bright) 0%,#1565b8 100%);color:var(--white);text-align:center}
.service-icon{position:absolute;left:51px;top:32px;width:189px;height:189px;border-radius:50%;background:var(--white);display:flex;align-items:center;justify-content:center}
.service-icon svg{width:100px;height:100px}
.service-name{position:absolute;top:250px;left:0;width:100%;font-size:22px}
.service-text{position:absolute;top:292px;left:50px;width:193px;font-size:13px;line-height:30px}
.service-go{position:absolute;left:124px;top:458px;width:46px;height:46px;border-radius:50%;background:var(--white);display:flex;align-items:center;justify-content:center}
.service-go span{width:13px;height:13px;border-radius:50%;background:var(--deep)}

/* about */
.about{position:absolute;left:0;top:1476px;width:1200px;height:502px;background:linear-gradient(120deg,#a9e1f4,var(--pale) 60%,#c6ecf8)}
.about-art{position:absolute;left:123px;top:52px;width:418px;height:398px}
.about-title{position:absolute;left:630px;top:70px;font-size:36px}
.about-text{position:absolute;left:628px;top:130px;width:452px;font-size:13.5px;line-height:30px;color:#222}
.about .btn{left:628px;top:329px}

/* news */
.news{position:absolute;left:0;top:1978px;width:1200px;height:880px}
.news .section-title{top:82px}
.post{position:absolute;width:298px}
.post-img{width:100%;height:209px}
.post-meta{font-size:15px;color:#333;margin:22px 0 0 22px}
.post-title{font-size:22px;line-height:30px;margin:10px 0 0 22px}
.post-feature{background:var(--white);box-shadow:0 4px 14px rgba(0,0,0,.15);height:303px;padding:34px 20px 0 20px}
.post-feature .post-meta,.post-feature .post-title{margin-left:0}
.post-feature .post-meta{margin-top:0}
.post-excerpt{font-size:13px;line-height:26px;margin-top:10px;color:#222}
.read-more{display:flex;align-items:center;gap:8px;margin-top:10px;font-family:"Baloo 2",sans-serif;font-weight:700;font-size:15px;color:var(--sky)}
.read-more span{width:12px;height:12px;border-radius:50%;background:var(--sky)}

/* footer */
.site-footer{position:absolute;left:0;top:2858px;width:1200px;height:391px;background:linear-gradient(180deg,#0a2036,var(--night));color:var(--white)}
.footer-wave{position:absolute;left:0;top:0;width:1200px;height:90px}
.footer-col{position:absolute;top:140px}
.footer-col h3{font-size:20px;margin-bottom:10px}
.footer-col p,.footer-col li{font-size:13px;line-height:26px}
.footer-col ul{list-style:none}
.footer-col li{display:flex;align-items:center;gap:8px}
.footer-col li svg{width:12px;height:12px;flex:none}
.subscribe{display:flex;width:330px;height:38px;margin-top:10px;border-radius:20px;background:var(--white);overflow:hidden}
.subscribe span{flex:1;padding-left:16px;line-height:38px;font-size:13px;color:#555}
.subscribe b{width:114px;background:var(--navy);border-radius:20px;text-align:center;line-height:38px;font-family:"Baloo 2",sans-serif;font-size:15px}
.footer-social{left:762px;top:254px}
.footer-social span{background:var(--white)}
.copyright{position:absolute;left:0;top:346px;width:1200px;text-align:center;font-size:13px}
</style>
</head>
<body>

<header class="site-header">
  <div class="brand"><span class="brand-dot"></span>VORPLEXA</div>
  <nav class="main-nav">
    <a>HOME</a><a class="caret">WHAT WE DO</a><a class="caret">RESOURCES</a><a class="caret">COMPANY</a><a>CONTACT US</a>
  </nav>
  <div class="nav-active"></div>
  <div class="social header-social" aria-label="Social links"><span></span><span></span><span></span><span></span></div>
</header>

<section class="hero">
  <div class="hero-photo" role="img" aria-label="Photo of hands typing on a laptop with glowing security interface overlay"></div>
  <h1 class="hero-title head">VORPLEXA EFFECTIVE<br>TECHNOLOGY MANAGEMENT</h1>
  <p class="hero-text">Lorem ipsum dolor sit amet, consectetur adipiscing elit, sed do eiusmod tempor incididunt ut labore et dolore magna aliqua.</p>
  <a class="btn">LEARN MORE <svg viewBox="0 0 14 14"><circle cx="7" cy="7" r="7" fill="#fff"/><path d="M5 3.5 8.5 7 5 10.5" stroke="#0455a3" stroke-width="2" fill="none"/></svg></a>
  <svg class="hero-wave" viewBox="0 0 1200 90" preserveAspectRatio="none">
    <path d="M0 56 C200 110 460 80 600 45 C820 -5 1000 0 1200 30 L1200 90 L0 90Z" fill="#fff"/>
    <path d="M600 45 C780 0 1000 0 1200 30 L1200 35 C1000 80 760 100 600 45Z" fill="#1fa3e3"/>
  </svg>
</section>

<section class="services">
  <h2 class="section-title head">WHAT WE DO</h2>

  <article class="service-card" style="left:135px">
    <div class="service-icon">
      <svg viewBox="0 0 100 100" fill="none" stroke="#1a8fd6" stroke-width="3">
        <path d="M28 70 a14 14 0 0 1 2-28 a20 20 0 0 1 38-4 a15 15 0 0 1 4 32Z"/>
        <path d="M40 70v14M52 70v18M64 70v12M40 40V22M52 36V16M64 40V22"/>
        <circle cx="40" cy="20" r="3"/><circle cx="52" cy="14" r="3"/><circle cx="64" cy="20" r="3"/>
      </svg>
    </div>
    <h3 class="service-name head">CLOUD ADOPTION</h3>
    <p class="service-text">Lorem ipsum dolor sit amet, consectetur adipiscing elit, sed do eiusmod tempor incididunt ut labore et dolore magna aliqua. Quis ipsum suspendisse ultrices</p>
    <a class="service-go"><span></span></a>
  </article>

  <article class="service-card" style="left:453px">
    <div class="service-icon">
      <svg viewBox="0 0 100 100" fill="none" stroke="#1a8fd6" stroke-width="3">
        <circle cx="52" cy="36" r="16"/><circle cx="52" cy="36" r="7"/>
        <path d="M52 14v6M52 52v6M30 36h6M68 36h6"/>
        <path d="M14 66h10v22H14ZM24 70h18c8 0 10 6 4 6h-10M24 86h26l26-16c4-3 0-8-4-6l-18 8"/>
      </svg>
    </div>
    <h3 class="service-name head">MANAGED SERVICES</h3>
    <p class="service-text">Lorem ipsum dolor sit amet, consectetur adipiscing elit, sed do eiusmod tempor incididunt ut labore et dolore magna aliqua. Quis ipsum suspendisse ultrices</p>
    <a class="service-go"><span></span></a>
  </article>

  <article class="service-card" style="left:769px">
    <div class="service-icon">
      <svg viewBox="0 0 100 100" fill="none" stroke="#1a8fd6" stroke-width="3.5">
        <circle cx="50" cy="50" r="14"/>
        <path d="M44 14h12l2 10 8 4 9-6 8 8-6 9 4 8 10 2v12l-10 2-4 8 6 9-8 8-9-6-8 4-2 10H44l-2-10-8-4-9 6-8-8 6-9-4-8-10-2V44l10-2 4-8-6-9 8-8 9 6 8-4Z"/>
      </svg>
    </div>
    <h3 class="service-name head">OPTIMISE</h3>
    <p class="service-text">Lorem ipsum dolor sit amet, consectetur adipiscing elit, sed do eiusmod tempor incididunt ut labore et dolore magna aliqua. Quis ipsum suspendisse ultrices</p>
    <a class="service-go"><span></span></a>
  </article>
</section>

<section class="about">
  <svg class="about-art" viewBox="0 0 418 398" role="img" aria-label="Photo of a team working at computer monitors in a server room, framed in a blue blob">
    <path d="M60 40 C140 -20 280 10 360 80 C420 140 420 260 360 330 C290 400 160 410 80 350 C10 300 -20 110 60 40Z" fill="#0a1ca0"/>
    <path d="M80 80 C150 30 290 60 340 130 C380 200 360 300 300 350 C230 400 120 390 70 320 C30 260 30 120 80 80Z" fill="#2a3a4e"/>
  </svg>
  <h2 class="about-title head">ABOUT US</h2>
  <p class="about-text">Lorem ipsum dolor sit amet, consectetur adipiscing elit, sed do eiusmod tempor incididunt ut labore et dolore magna aliqua. Ut enim ad minim veniam, quis nostrud exercitation ullamco laboris nisi ut aliquip ex ea commodo consequat. Duis aute irure dolor in reprehenderit in voluptate velit esse cillum dolore eu fugiat nulla pariatur. Excepteur sint occaecat cupidatat non proident, sunt in culpa qui officia deserunt mollit anim id est laborum.</p>
  <a class="btn">LEARN MORE <svg viewBox="0 0 14 14"><circle cx="7" cy="7" r="7" fill="#fff"/><path d="M5 3.5 8.5 7 5 10.5" stroke="#0455a3" stroke-width="2" fill="none"/></svg></a>
</section>

<section class="news">
  <h2 class="section-title head">NEWS &amp; BLOG</h2>

  <article class="post" style="left:151px;top:178px">
    <div class="post-img" style="height:303px;background:linear-gradient(135deg,#1c2a4a,#0b1020)" role="img" aria-label="Photo of a keyboard with a padlock login graphic"></div>
  </article>

  <article class="post post-feature" style="left:451px;top:178px">
    <p class="post-meta">May 25 2021</p>
    <h3 class="post-title head">LOREM IPSUM DOLOR<br>SIT AMET</h3>
    <p class="post-excerpt">Lorem ipsum dolor sit amet, consectetur adipiscing elit, sed do eiusmod tempor incididunt ut labore et dolore magna aliqua. Quis ipsum suspendisse ultrices gravida. Risus commodo</p>
    <a class="read-more">LEARN MORE <span></span></a>
  </article>

  <article class="post" style="left:751px;top:178px">
    <div class="post-img" style="background:linear-gradient(135deg,#2a3a4c,#141c28)" role="img" aria-label="Photo of a laptop with padlock graphics"></div>
    <p class="post-meta">May 25 2021</p>
    <h3 class="post-title head">LOREM IPSUM DOLOR<br>SIT AMET</h3>
  </article>

  <article class="post" style="left:151px;top:491px">
    <div class="post-img" style="background:linear-gradient(135deg,#1a2840,#0c1424)" role="img" aria-label="Photo of a team at work desks"></div>
    <p class="post-meta">May 25 2021</p>
    <h3 class="post-title head">LOREM IPSUM DOLOR<br>SIT AMET</h3>
  </article>

  <article class="post" style="left:451px;top:491px">
    <div class="post-img" style="background:linear-gradient(135deg,#0f2a3a,#0a1a1e)" role="img" aria-label="Photo of an engineer in a server room"></div>
    <p class="post-meta">May 25 2021</p>
    <h3 class="post-title head">LOREM IPSUM DOLOR<br>SIT AMET</h3>
  </article>

  <article class="post" style="left:751px;top:491px">
    <div class="post-img" style="background:radial-gradient(circle at 50% 45%,#5a6e8a,#0c1630 70%)" role="img" aria-label="Photo of a hand with a cloud padlock graphic"></div>
    <p class="post-meta">May 25 2021</p>
    <h3 class="post-title head">LOREM IPSUM DOLOR<br>SIT AMET</h3>
  </article>
</section>

<footer class="site-footer">
  <svg class="footer-wave" viewBox="0 0 1200 90" preserveAspectRatio="none">
    <path d="M0 0 H1200 V8 C1000 -5 780 20 600 55 C420 90 200 60 0 45Z" fill="#fff"/>
    <path d="M0 45 C150 10 400 10 600 55 C420 90 200 85 0 45Z" fill="#1fa3e3"/>
  </svg>
  <div class="footer-col" style="left:122px">
    <h3 class="head">ABOUT US</h3>
    <p style="width:225px">Lorem ipsum dolor sit amet, consectetur adipiscing elit, sed do eiusmod tempor incididunt</p>
  </div>
  <div class="footer-col" style="left:446px">
    <h3 class="head">CONTACT US</h3>
    <ul>
      <li><svg viewBox="0 0 12 12"><path d="M6 0a4 4 0 0 1 4 4c0 3-4 8-4 8S2 7 2 4a4 4 0 0 1 4-4Z" fill="#fff"/></svg>Lorem ipsum dolor sit amet, consectetur</li>
      <li><svg viewBox="0 0 12 12"><path d="M2 1l3 0 1 3-2 1a7 7 0 0 0 3 3l1-2 3 1v3c-6 0-9-4-9-9Z" fill="#fff"/></svg>555-014-2290</li>
      <li><svg viewBox="0 0 12 12"><path d="M0 2h12v8H0Z" fill="#fff"/><path d="M0 2l6 4 6-4" stroke="#06142a" fill="none"/></svg>info@vorplexa.com</li>
    </ul>
  </div>
  <div class="footer-col" style="left:754px">
    <h3 class="head">SUBSCRIBE TO OUR NEWSLETTER</h3>
    <div class="subscribe"><span>Enter Your Email</span><b>SUBSCRIBE</b></div>
  </div>
  <div class="social footer-social" aria-label="Social links"><span></span><span></span><span></span><span></span></div>
  <p class="copyright">© Copyrights 2021 Vorplexa Effective Technology Management &nbsp;|&nbsp; All Rights Reserved</p>
</footer>

</body>
</html>
```